Bright Path Mentors Needs A New Website Design

We need a 8 page website designed for "Bright Path Mentors .ca" similar in design to: "keystone learning hub .com".

The winner/successful candidate on the home page will be asked to complete the following inner pages to complete the project:

About Us
Philosophy
How We Work
Work With Us
Blog
Find A Tutor
Contact

Target Market(s)

Tutoring business clients/children

Industry/Entity Type

Education

Number of Pages Required

5+ page

Font styles to use
Sans Serif

Requirements
Must have
• The attached logo included of course. Similar design to the design provided above in the brief. Clear high quality high resolution images of children in school settings.

```html
<!DOCTYPE html>
<html lang="en">
<head>
<meta charset="utf-8">
<title>Bright Path Mentors</title>
<link href="https://fonts.googleapis.com/css2?family=Lora:wght@400;700&display=swap" rel="stylesheet">
<style>
:root{
  --orange:#f7941d;
  --blue:#2e3192;
  --navy:#1f2758;
  --text:#555;
  --muted:#888;
  --line:#d5d5d5;
  --white:#fff;
}
*{margin:0;padding:0;box-sizing:border-box}
html,body{width:1200px;height:2853px;overflow:hidden}
body{font-family:'Lora',Georgia,serif;color:var(--text);background:var(--white);position:relative}
section,header,footer{position:absolute;left:0;width:1200px}
.abs{position:absolute}

/* header */
.site-header{top:0;height:100px;background:var(--white)}
.brand{left:130px;top:0;width:140px;height:200px;background:var(--white);z-index:5;display:flex;flex-direction:column;align-items:center;justify-content:center;gap:10px;box-shadow:0 3px 6px rgba(0,0,0,.08)}
.brand-mark{width:28px;height:28px;border-radius:50%;background:var(--orange)}
.brand-name{font-weight:700;color:var(--blue);font-size:21px;line-height:1.15;text-align:center}
.social{display:flex;gap:6px}
.social span{width:26px;height:26px;border-radius:50%;display:block}
.header-social{left:536px;top:36px}
.header-social span{background:var(--blue)}
.call{left:640px;top:30px;width:134px;text-align:right;line-height:1.2}
.call small{display:block;font-size:11px;color:#333}
.call strong{display:block;font-size:18px;color:var(--orange);font-weight:400;white-space:nowrap}
.call-icon{left:782px;top:28px;width:42px;height:42px;border-radius:50%;background:#eee}
.search{left:850px;top:28px;width:217px;height:42px;border:1px solid var(--line);font-size:12px;color:#999;padding:13px 14px}
.search svg{position:absolute;right:12px;top:13px}

.main-nav{position:absolute;left:0;width:1200px;top:100px;height:31px;background:var(--blue)}
.main-nav ul{list-style:none;display:flex;position:absolute;left:272px;top:0;height:31px}
.main-nav li{color:var(--white);font-size:11px;line-height:31px;padding:0 19px;text-transform:uppercase}
.main-nav li.active{background:var(--orange)}

/* hero */
.hero{top:131px;height:481px}
.hero-photo{left:0;top:0;width:1200px;height:481px;background:linear-gradient(120deg,#cfc6ba 0%,#a89d92 35%,#6a7281 65%,#e4ddd4 100%)}
.hero-tag{left:131px;top:236px;width:343px;background:rgba(46,49,146,.78);color:var(--white);font-weight:700;font-size:21px;line-height:1.4;padding:12px 14px;text-transform:uppercase}
.dots{left:570px;top:448px;display:flex;gap:6px}
.dots i{width:8px;height:8px;border-radius:50%;background:rgba(255,255,255,.6);display:block}
.dots i:first-child{background:var(--white)}

/* promo */
.promo{top:612px;height:200px;background:var(--orange);text-align:center}
.promo h2{color:var(--white);font-size:32px;font-weight:700;margin-top:50px;text-transform:uppercase}
.btn-blue{display:inline-block;margin-top:18px;background:var(--blue);color:var(--white);font-size:21px;padding:11px 26px;border-radius:3px;font-weight:700;text-transform:uppercase}

/* welcome */
.welcome{top:812px;height:417px}
.welcome h1{left:133px;top:58px;width:500px;font-size:25px;color:var(--blue);text-transform:uppercase;white-space:nowrap}
.welcome .copy{left:133px;top:108px;width:495px;font-size:12.5px;line-height:1.7;color:var(--muted)}
.welcome .copy p+p{margin-top:18px}
.welcome .media{left:666px;top:40px;width:400px;height:342px;background:linear-gradient(160deg,#f3ece4,#e8d9c8 60%,#d8c3a8)}
.watch-btn{left:190px;top:28px;border:2px solid var(--white);color:var(--white);font-size:13px;padding:8px 14px;background:rgba(0,0,0,.3);display:flex;align-items:center;gap:8px}

/* testimonials */
.testimonials{top:1229px;height:199px;background:var(--blue);text-align:center;color:var(--white)}
.testimonials h2{color:var(--orange);font-size:31px;margin-top:28px}
.testimonials blockquote{font-size:17px;line-height:1.45;margin-top:8px}
.testimonials cite{display:block;color:var(--orange);font-style:normal;font-size:15px;margin-top:6px}
.testimonials .place{font-size:10px;color:var(--orange);text-transform:uppercase}
.arrow{top:88px}

/* features */
.features{top:1428px;height:265px}
.feature{top:55px;width:300px;text-align:center}
.feature svg{display:block;margin:0 auto 14px}
.feature h3{color:var(--orange);font-size:21px;line-height:1.3;text-transform:uppercase}
.feature p{font-size:12.5px;color:var(--muted);line-height:1.6;margin-top:12px}

/* blog */
.blog{top:1693px;height:399px;background:var(--orange)}
.blog h2{left:0;width:100%;text-align:center;color:var(--white);font-size:31px;top:28px}
.card{top:85px;width:295px;height:272px;background:var(--white)}
.card .thumb{height:175px}
.card p{font-size:15px;color:#333;line-height:1.4;padding:16px 14px 6px}
.card a{font-size:9px;color:var(--orange);padding:0 14px;text-transform:uppercase;text-decoration:none}

/* find */
.find{top:2092px;height:225px}
.find h2{left:0;width:100%;text-align:center;color:var(--orange);font-size:31px;top:48px}
.field{top:100px;width:242px}
.field label{display:block;font-size:15px;color:#444;margin-bottom:6px}
.field .box{height:45px;border:1px solid var(--line);font-size:12px;color:#999;padding:14px 16px;position:relative}
.field .box svg{position:absolute;right:14px;top:16px}
.btn-orange{background:var(--orange);color:var(--white);font-weight:700;text-transform:uppercase;text-align:center}
.find .btn-orange{left:948px;top:124px;width:119px;height:45px;line-height:45px;font-size:15px}

/* contact */
.contact{top:2317px;height:441px;color:var(--white)}
.contact-photo{left:0;top:0;width:1200px;height:441px;background:linear-gradient(135deg,#3a3ea6 0%,#2e3192 50%,#353a9e 100%)}
.contact h2{left:0;width:100%;text-align:center;font-size:31px;top:44px}
.contact h3{font-size:25px;font-weight:400}
.loc{font-size:14px;line-height:23px;list-style:none}
.loc li::before{content:"•";margin-right:6px}
.divider{left:601px;top:115px;width:1px;height:290px;background:rgba(255,255,255,.3)}
.rule{height:1px;background:rgba(255,255,255,.3)}
.addr{font-size:13px;display:flex;align-items:center;gap:8px;white-space:nowrap}
.contact .social span{background:var(--white)}
.form-label{font-size:12px}
.form-input{background:var(--white);height:40px;color:#999;font-size:11px;padding:13px 12px}
.form-input svg{position:absolute;right:12px;top:16px}
.contact .btn-orange{left:806px;top:352px;width:90px;height:38px;line-height:38px;font-size:15px}

/* footer */
.site-footer{top:2758px;height:95px;background:var(--navy);text-align:center;color:#c8c9dd}
.site-footer .footer-links{font-size:11px;margin-top:22px}
.site-footer .footer-links span{margin:0 6px}
.site-footer p{font-size:11px;margin-top:16px}
</style>
</head>
<body>

<header class="site-header">
  <div class="brand abs">
    <span class="brand-mark"></span>
    <span class="brand-name">Bright Path<br>Mentors</span>
  </div>
  <div class="social header-social abs"><span></span><span></span><span></span></div>
  <div class="call abs"><small>Call us on</small><strong>1-855-300-7142</strong></div>
  <div class="call-icon abs">
    <svg width="42" height="42" viewBox="0 0 42 42"><path d="M16 14c1-1 2 0 3 2l1 2c0 1-1 2-1 2 1 2 2 3 4 4 0 0 1-1 2-1l2 1c2 1 3 2 2 3-2 2-4 2-7 0-3-2-5-4-7-7-1-3-1-5 1-6z" fill="#888"/></svg>
  </div>
  <div class="search abs">Search
    <svg width="14" height="14" viewBox="0 0 14 14"><circle cx="6" cy="6" r="4.5" fill="none" stroke="#f7941d" stroke-width="2"/><path d="M9.5 9.5l3.5 3.5" stroke="#f7941d" stroke-width="2"/></svg>
  </div>
</header>

<nav class="main-nav">
  <ul>
    <li class="active">Home</li><li>About Us</li><li>Philosophy</li><li>How We Work</li><li>Work With Us</li><li>Blog</li><li>Find A Tutor</li><li>Contact</li>
  </ul>
</nav>

<section class="hero">
  <div class="hero-photo abs" role="img" aria-label="Photo of a smiling schoolboy writing at a classroom desk with classmates behind him"></div>
  <div class="hero-tag abs">All subjects, all grades,<br>available on-call when<br>you need us most</div>
  <div class="dots abs"><i></i><i></i><i></i><i></i></div>
</section>

<section class="promo">
  <h2>First session just $7! All subjects! All grades!</h2>
  <span class="btn-blue">Book Now</span>
</section>

<section class="welcome">
  <h1 class="abs">Welcome to Bright Path Mentors</h1>
  <div class="copy abs">
    <p>Donec ac tincidunt augue, quis fringilla lectus. Sed eu porttitor ex. Sed sit amet orci scelerisque, auctor justo at, efficitur arcu. Donec blandit laoreet iaculis. Vivamus tincidunt vestibulum tortor lacinia commodo. Vestibulum et nisl ac justo blandit lobortis. Nam ac est efficitur, suscipit quam ac, ultricies neque. Integer et velit pretium, pharetra libero ultricies, maximus mauris. Nunc ac dapibus lectus, quis tincidunt est. Nulla faucibus tincidunt ultrices. Integer lobortis hendrerit velit, a vulputate dui imperdiet ac. Donec non velit ut velit ultrices mattis.</p>
    <p>Cras lacinia malesuada ornare. Donec nec velit quis turpis molestie lobortis eu a nisi. In vulputate felis nec diam tempor, sit amet dapibus enim hendrerit. In tristique rutrum tellus, non tincidunt enim porttitor at. Fusce facilisis faucibus massa. Etiam gravida, justo id aliquam consectetur, elit magna feugiat nisi.</p>
  </div>
  <div class="media abs" role="img" aria-label="Illustration of a teacher pointing at a chalkboard while two children solve sums">
    <div class="watch-btn abs">
      <svg width="14" height="14" viewBox="0 0 14 14"><circle cx="7" cy="7" r="6" fill="none" stroke="#fff" stroke-width="1.5"/><path d="M5.5 4.5l4 2.5-4 2.5z" fill="#fff"/></svg>
      WATCH VIDEO
    </div>
  </div>
</section>

<section class="testimonials">
  <h2>TESTIMONIALS</h2>
  <blockquote>“ Clara Whitmore Dear Ms. Whitmore:<br>RE: Highest Recommendation for Tutoring Services I take this opportunity to give the highest... ”</blockquote>
  <cite>~ Dana M.</cite>
  <div class="place">Vaughan, Ontario</div>
  <svg class="abs arrow" style="left:22px" width="14" height="26" viewBox="0 0 14 26"><path d="M12 2L2 13l10 11" fill="none" stroke="#fff" stroke-width="2"/></svg>
  <svg class="abs arrow" style="left:1162px" width="14" height="26" viewBox="0 0 14 26"><path d="M2 2l10 11L2 24" fill="none" stroke="#fff" stroke-width="2"/></svg>
</section>

<section class="features">
  <div class="feature abs" style="left:126px">
    <svg width="48" height="38" viewBox="0 0 48 38"><circle cx="24" cy="19" r="17" fill="#f7941d"/><path d="M19 11l13 8-13 8z" fill="#fff"/></svg>
    <h3>Highly-credentialed<br>tutors</h3>
    <p>We require the most rigorous qualifications of<br>our tutors, in addition to a background check.</p>
  </div>
  <div class="feature abs" style="left:449px">
    <svg width="38" height="40" viewBox="0 0 38 40"><path d="M6 2h18l8 8v28H6z" fill="none" stroke="#f7941d" stroke-width="2.5"/><path d="M12 17h14M12 23h14M12 29h14" stroke="#f7941d" stroke-width="2.5"/></svg>
    <h3>Personalized lesson<br>plans</h3>
    <p>We deliver personally tailored lessons from<br>exceptional tutors in a one-on-one setting.</p>
  </div>
  <div class="feature abs" style="left:771px">
    <svg width="40" height="40" viewBox="0 0 40 40"><circle cx="20" cy="20" r="18" fill="#f7941d"/><path d="M11 20l6 6 12-13" fill="none" stroke="#fff" stroke-width="3.5"/></svg>
    <h3>Money-back &amp; tutor<br>guarantee</h3>
    <p>We offer an unparalleled satisfaction guarantee<br>with our tutors.</p>
  </div>
</section>

<section class="blog">
  <h2 class="abs">BLOG</h2>
  <svg class="abs" style="left:22px;top:190px" width="14" height="26" viewBox="0 0 14 26"><path d="M12 2L2 13l10 11" fill="none" stroke="#fff" stroke-width="2"/></svg>
  <svg class="abs" style="left:1162px;top:190px" width="14" height="26" viewBox="0 0 14 26"><path d="M2 2l10 11L2 24" fill="none" stroke="#fff" stroke-width="2"/></svg>
  <article class="card abs" style="left:133px">
    <div class="thumb" role="img" aria-label="Photo of a girl smiling at her classroom desk" style="background:linear-gradient(135deg,#d9b49a,#a5624d 60%,#7b3a30)"></div>
    <p>Donec ac tincidunt augue, quis fringilla lectus amet orci scelerisque</p>
    <a href="#">Read more</a>
  </article>
  <article class="card abs" style="left:453px">
    <div class="thumb" role="img" aria-label="Photo of students in uniforms working at rows of desks" style="background:linear-gradient(135deg,#7a6f66,#3d3a44 55%,#9a8f88)"></div>
    <p>Donec ac tincidunt augue, quis fringilla lectus amet orci scelerisque</p>
    <a href="#">Read more</a>
  </article>
  <article class="card abs" style="left:772px">
    <div class="thumb" role="img" aria-label="Photo of smiling boys writing together in class" style="background:linear-gradient(135deg,#e6d7c6,#b55a3c 55%,#6b7a8f)"></div>
    <p>Donec ac tincidunt augue, quis fringilla lectus amet orci scelerisque</p>
    <a href="#">Read more</a>
  </article>
</section>

<section class="find">
  <h2 class="abs">FIND A TUTOR</h2>
  <div class="field abs" style="left:133px"><label>City</label>
    <div class="box">Select<svg width="10" height="13" viewBox="0 0 10 13"><path d="M5 12C2 8 1 6 1 5a4 4 0 018 0c0 1-1 3-4 7z" fill="#999"/><circle cx="5" cy="5" r="1.5" fill="#fff"/></svg></div></div>
  <div class="field abs" style="left:405px"><label>Subject</label>
    <div class="box">Select<svg width="12" height="8" viewBox="0 0 12 8"><path d="M1 1l5 5 5-5" fill="none" stroke="#999" stroke-width="1.5"/></svg></div></div>
  <div class="field abs" style="left:676px"><label>Lesson</label>
    <div class="box">Select<svg width="12" height="8" viewBox="0 0 12 8"><path d="M1 1l5 5 5-5" fill="none" stroke="#999" stroke-width="1.5"/></svg></div></div>
  <div class="btn-orange abs">Find Now</div>
</section>

<section class="contact">
  <div class="contact-photo abs" role="img" aria-label="Blue-tinted photo of a classroom with students raising their hands"></div>
  <h2 class="abs">CONTACT US</h2>
  <h3 class="abs" style="left:133px;top:110px">Locations</h3>
  <ul class="loc abs" style="left:143px;top:146px"><li>Toronto</li><li>Richmond Hill</li></ul>
  <ul class="loc abs" style="left:285px;top:146px"><li>Markham</li><li>Vaughan</li></ul>
  <ul class="loc abs" style="left:403px;top:146px"><li>Newmarket</li><li>Aurora</li></ul>
  <div class="rule abs" style="left:133px;top:200px;width:440px"></div>
  <h3 class="abs" style="left:133px;top:218px">Office Address</h3>
  <div class="addr abs" style="left:133px;top:254px"><svg width="9" height="12" viewBox="0 0 10 13"><path d="M5 12C2 8 1 6 1 5a4 4 0 018 0c0 1-1 3-4 7z" fill="#fff"/></svg>1280 Maple Avenue, Suite 210</div>
  <div class="addr abs" style="left:150px;top:279px">Toronto - Ontario</div>
  <div class="addr abs" style="left:342px;top:254px"><svg width="11" height="11" viewBox="0 0 11 11"><path d="M2 1l2 0 1 3-1 1c1 2 2 3 4 4l1-1 3 1v2c-5 0-10-5-10-10z" fill="#fff"/></svg>1-855-300-7142</div>
  <div class="addr abs" style="left:342px;top:279px"><svg width="11" height="9" viewBox="0 0 11 9"><rect width="11" height="9" fill="#fff"/><path d="M0 0l5.5 5L11 0" fill="none" stroke="#2e3192"/></svg>info@brightpathmentors.ca</div>
  <div class="addr abs" style="left:498px;top:254px"><svg width="10" height="10" viewBox="0 0 10 10"><rect width="10" height="10" fill="#fff"/></svg>M4B 2K7</div>
  <div class="rule abs" style="left:133px;top:306px;width:440px"></div>
  <h3 class="abs" style="left:133px;top:322px">Share us on</h3>
  <div class="social abs" style="left:133px;top:364px;gap:10px"><span></span><span></span><span></span></div>

  <div class="divider abs"></div>

  <span class="form-label abs" style="left:643px;top:112px">Name</span>
  <div class="form-input abs" style="left:643px;top:129px;width:200px"></div>
  <span class="form-label abs" style="left:867px;top:112px">Email</span>
  <div class="form-input abs" style="left:867px;top:129px;width:200px"></div>
  <span class="form-label abs" style="left:643px;top:192px">Phone</span>
  <div class="form-input abs" style="left:643px;top:209px;width:200px"></div>
  <span class="form-label abs" style="left:867px;top:192px">Subject</span>
  <div class="form-input abs" style="left:867px;top:209px;width:200px">Select<svg width="10" height="7" viewBox="0 0 12 8"><path d="M1 1l5 5 5-5" fill="none" stroke="#999" stroke-width="1.5"/></svg></div>
  <span class="form-label abs" style="left:643px;top:272px">Message</span>
  <div class="form-input abs" style="left:643px;top:289px;width:424px"></div>
  <div class="btn-orange abs">Submit</div>
</section>

<footer class="site-footer">
  <div class="footer-links">Home<span>|</span>About Us<span>|</span>Philosophy<span>|</span>How We Work<span>|</span>Work With Us<span>|</span>Blog<span>|</span>Find A Tutor<span>|</span>Contact</div>
  <p>Copyright © 2016 Bright Path Mentors. All rights reserved.</p>
</footer>

</body>
</html>
```